FinTech company looking to revamp and expand client-facing interface for our financial models

Pellworth Engines currently has a very simple website that allows clients to interact with our financial models. We are looking to completely redesign the current site and add several extra pages to provide extra functionality. We want the design to have a modern, slick feel, that will work on both a desktop or a tablet. It should be straightforward for clients to move between different pages at any time, and clear from the layout how to interact with the more advanced features. We have included screenshots of existing pages in the attached design brief, as well as sketches of the functionality required by the new pages, but can't provide a direct link to the current site.
Target Market(s)
Professional investors that will be paying to access the interface
Industry/Entity Type
Finance
Number of Pages Required
4 page
Colors
Designer to choose colors to be used in the design.
Look and feel
Each slider illustrates characteristics of the customer's brand and the style your logo design should communicate.

```html
<!DOCTYPE html>
<html lang="en">
<head>
<meta charset="utf-8">
<title>Pellworth Engines – Model Interface</title>
<link rel="stylesheet" href="https://fonts.googleapis.com/css2?family=Open+Sans:wdth,wght@75..100,400..800&display=swap">
<style>
  :root{
    --page:#e8e8e8;
    --ink:#1a1a1a;
    --black:#000;
    --nav-blue:#0e4c99;
    --nav-line:#1d5aa6;
    --table-head:#0f4d9c;
    --row-hi:#3d95ee;
    --row-alt:#dcdcdc;
    --row-alt-light:#ececec;
    --content:#f8f9fc;
    --content-warm:#fdfbfb;
    --btn-blue:#0e4c99;
    --btn-orange:#f0800f;
    --active-tab:#1e1e1e;
    --grid:#9a9a9a;
  }
  *{box-sizing:border-box;margin:0;padding:0}
  html,body{width:784px;height:1200px;overflow:hidden}
  body{background:var(--page);font-family:"Open Sans",Arial,sans-serif;color:var(--ink);position:relative}

  .screen{position:absolute;left:65px;width:654px;background:var(--content)}
  .screen--one{top:67px;height:342px}
  .screen--two{top:426px;height:342px}
  .screen--three{top:793px;height:340px;background:var(--content-warm)}

  /* legacy screen header */
  .topbar{height:42px;background:var(--black);position:relative;color:#fff}
  .brand{position:absolute;left:53px;top:11px;font-size:14px;font-weight:700;letter-spacing:.1px}
  .btn{position:absolute;top:10px;width:66px;height:21px;font-size:8.5px;font-weight:700;color:#fff;display:flex;align-items:center;justify-content:center}
  .btn--login{left:461px;background:var(--btn-blue)}
  .btn--signin{left:534px;background:var(--btn-orange)}

  .sidebar{position:absolute;left:0;top:42px;bottom:0;width:100px;background:var(--nav-blue);color:#fff}
  .sidebar li{list-style:none;height:19.6px;border-bottom:1px solid var(--nav-line);font-size:8px;display:flex;align-items:center;padding-left:9px;gap:3px}
  .sidebar li.section{font-weight:700}
  .sidebar svg{flex:none}

  .main{position:absolute;left:100px;top:42px;right:0;bottom:0}
  .threshold{position:absolute;left:22px;display:flex;align-items:center;font-size:8px}
  .threshold span{width:76px}
  .field{width:101px;height:17px;background:#fff;border:1px solid #cfcfcf;font-size:7.5px;padding-left:4px;display:flex;align-items:center}
  .export{position:absolute;left:22px;top:106px;font-size:11px;font-weight:700}

  .grid{position:absolute;border-collapse:collapse;table-layout:fixed}
  .grid--factors{left:22px;top:129px;width:478px;font-size:8.5px}
  .grid--factors th{height:26px;background:var(--table-head);color:#fff;font-weight:400}
  .grid--factors td{height:26px;text-align:center;border-left:1px solid var(--grid)}
  .grid--factors th:first-child,.grid--factors td:first-child{text-align:left;padding-left:5px;border-left:none}
  .grid--factors tr{background:#fff}
  .grid--factors tr.is-selected{background:var(--row-hi);color:#fff}
  .grid--factors tr.is-alt{background:var(--row-alt)}

  /* new screen */
  .topnav{height:42px;background:var(--black);position:relative;color:#fff;font-weight:700;font-size:11px}
  .topnav a{position:absolute;top:0;height:42px;display:flex;align-items:center;color:#fff;text-decoration:none}
  .topnav .tab--active{background:var(--active-tab);padding:0 5px}
  .quality{position:absolute;top:73px;left:43px;font-size:11px;font-weight:700}
  .qlabel{position:absolute;top:72px;font-size:12px}
  .qfield{position:absolute;top:72px;width:82px;height:17px;background:#fff;border:1px solid #bdbdbd;font-size:8px;padding-left:3px;display:flex;align-items:center}
  .export--new{left:45px;top:101px}

  .grid--models{left:44px;top:117px;width:566px;font-stretch:75%;font-size:7.2px}
  .grid--models th{height:32px;background:var(--table-head);color:#fff;font-weight:700;font-size:8.2px}
  .grid--models th.sort{font-size:10px}
  .grid--models td{height:33px;text-align:center;border-left:1px solid var(--grid);line-height:1.3}
  .grid--models td:first-child{border-left:none}
  .grid--models tbody tr{background:#fff}
  .grid--models tbody tr:nth-child(even){background:var(--row-alt-light)}
</style>
</head>
<body>

<!-- Screen 1 -->
<section class="screen screen--one">
  <header class="topbar">
    <div class="brand">PELLWORTH ENGINES</div>
    <div class="btn btn--login">LOG IN</div>
    <div class="btn btn--signin">SIGN IN</div>
  </header>
  <nav class="sidebar">
    <ul>
      <li class="section">FACTORS</li>
      <li class="section">250D</li>
      <li class="section">83D</li>
      <li class="section">42D</li>
      <li class="section"><svg width="8" height="8" viewBox="0 0 10 10"><path d="M5 1 L9.5 5 H8 V9 H6 V6.5 H4 V9 H2 V5 H.5Z" fill="#fff"/></svg>MODELS <svg width="7" height="5" viewBox="0 0 7 5"><path d="M.5 1 L3.5 4 L6.5 1" stroke="#fff" fill="none"/></svg></li>
      <li>Equities</li>
      <li>Etfs</li>
      <li>Pairs</li>
      <li>Etf pairs</li>
      <li>Factors</li>
      <li class="section"><svg width="8" height="8" viewBox="0 0 10 10"><circle cx="5" cy="5" r="4.2" stroke="#fff" fill="none"/><circle cx="5" cy="5" r="1.4" fill="#fff"/></svg>SENSITIVITIES <svg width="5" height="7" viewBox="0 0 5 7"><path d="M1 .5 L4 3.5 L1 6.5" stroke="#fff" fill="none"/></svg></li>
      <li class="section"><svg width="8" height="8" viewBox="0 0 10 10"><path d="M5 .5 L6.3 3.7 L9.7 3.9 L7.1 6.1 L7.9 9.5 L5 7.6 L2.1 9.5 L2.9 6.1 L.3 3.9 L3.7 3.7Z" fill="#fff"/></svg>FAVOURITES &nbsp; <svg width="5" height="7" viewBox="0 0 5 7"><path d="M1 .5 L4 3.5 L1 6.5" stroke="#fff" fill="none"/></svg></li>
    </ul>
  </nav>
  <main class="main">
    <div class="threshold" style="top:23px"><span>Stat 1 threshold</span><div class="field">-10</div></div>
    <div class="threshold" style="top:51px"><span>Stat 2 threshold</span><div class="field">-10</div></div>
    <div class="threshold" style="top:79px"><span>Stat 3 threshold</span><div class="field">-10</div></div>
    <div class="export">EXPORT</div>
    <table class="grid grid--factors">
      <colgroup><col style="width:53px"><col style="width:48px"><col style="width:89px"><col style="width:48px"><col style="width:47px"><col style="width:48px"><col style="width:48px"><col style="width:48px"><col style="width:49px"></colgroup>
      <thead><tr><th>Factor</th><th>ID</th><th>Sector</th><th>Stat 1</th><th>Stat 2</th><th>Stat 3</th><th>Stat 4</th><th>Stat 5</th><th>Stat 6</th></tr></thead>
      <tbody>
        <tr><td>Factor 1</td><td>Model 1</td><td>Materials</td><td>1.4</td><td>0.1</td><td>-3.1</td><td>0.7</td><td>30.2</td><td>0.9</td></tr>
        <tr class="is-selected"><td>Factor 2</td><td>Model 1</td><td>Materials</td><td>2.8</td><td>0.1</td><td>6.1</td><td>100</td><td>30.2</td><td>0.9</td></tr>
        <tr><td>Factor 3</td><td>Model 1</td><td>Materials</td><td>-3.7</td><td>2.7</td><td>-7.2</td><td>100</td><td>30.2</td><td>0.9</td></tr>
        <tr class="is-alt"><td>Factor 1</td><td>Model 2</td><td>Materials</td><td>2.8</td><td>0.2</td><td>2.7</td><td>0.5</td><td>32.9</td><td>0.5</td></tr>
        <tr><td>Factor 2</td><td>Model 2</td><td>Materials</td><td>0.8</td><td>0.3</td><td>2.5</td><td>0.5</td><td>32.9</td><td>-0.5</td></tr>
      </tbody>
    </table>
  </main>
</section>

<!-- Screen 2 -->
<section class="screen screen--two">
  <header class="topbar">
    <div class="brand">PELLWORTH ENGINES</div>
    <div class="btn btn--login">LOG IN</div>
    <div class="btn btn--signin">SIGN IN</div>
  </header>
  <nav class="sidebar">
    <ul>
      <li class="section">FACTORS</li>
      <li class="section">250D</li>
      <li class="section">83D</li>
      <li class="section">42D</li>
      <li class="section"><svg width="8" height="8" viewBox="0 0 10 10"><path d="M5 1 L9.5 5 H8 V9 H6 V6.5 H4 V9 H2 V5 H.5Z" fill="#fff"/></svg>MODELS <svg width="7" height="5" viewBox="0 0 7 5"><path d="M.5 1 L3.5 4 L6.5 1" stroke="#fff" fill="none"/></svg></li>
      <li>Equities</li>
      <li>Etfs</li>
      <li>Pairs</li>
      <li>Etf pairs</li>
      <li>Factors</li>
      <li class="section"><svg width="8" height="8" viewBox="0 0 10 10"><circle cx="5" cy="5" r="4.2" stroke="#fff" fill="none"/><circle cx="5" cy="5" r="1.4" fill="#fff"/></svg>SENSITIVITIES <svg width="5" height="7" viewBox="0 0 5 7"><path d="M1 .5 L4 3.5 L1 6.5" stroke="#fff" fill="none"/></svg></li>
      <li class="section"><svg width="8" height="8" viewBox="0 0 10 10"><path d="M5 .5 L6.3 3.7 L9.7 3.9 L7.1 6.1 L7.9 9.5 L5 7.6 L2.1 9.5 L2.9 6.1 L.3 3.9 L3.7 3.7Z" fill="#fff"/></svg>FAVOURITES &nbsp; <svg width="5" height="7" viewBox="0 0 5 7"><path d="M1 .5 L4 3.5 L1 6.5" stroke="#fff" fill="none"/></svg></li>
    </ul>
  </nav>
  <main class="main">
    <div class="threshold" style="top:23px"><span>Stat 1 threshold</span><div class="field">-10</div></div>
    <div class="threshold" style="top:51px"><span>Stat 2 threshold</span><div class="field">-10</div></div>
    <div class="threshold" style="top:79px"><span>Stat 3 threshold</span><div class="field">-10</div></div>
    <div class="export">EXPORT</div>
    <table class="grid grid--factors">
      <colgroup><col style="width:53px"><col style="width:48px"><col style="width:89px"><col style="width:48px"><col style="width:47px"><col style="width:48px"><col style="width:48px"><col style="width:48px"><col style="width:49px"></colgroup>
      <thead><tr><th>Factor</th><th>ID</th><th>Sector</th><th>Stat 1</th><th>Stat 2</th><th>Stat 3</th><th>Stat 4</th><th>Stat 5</th><th>Stat 6</th></tr></thead>
      <tbody>
        <tr><td>Factor 1</td><td>Model 1</td><td>Materials</td><td>1.4</td><td>0.1</td><td>-3.1</td><td>0.7</td><td>30.2</td><td>0.9</td></tr>
        <tr class="is-selected"><td>Factor 2</td><td>Model 1</td><td>Materials</td><td>2.8</td><td>0.1</td><td>6.1</td><td>100</td><td>30.2</td><td>0.9</td></tr>
        <tr><td>Factor 3</td><td>Model 1</td><td>Materials</td><td>-3.7</td><td>2.7</td><td>-7.2</td><td>100</td><td>30.2</td><td>0.9</td></tr>
        <tr class="is-alt"><td>Factor 1</td><td>Model 2</td><td>Materials</td><td>2.8</td><td>0.2</td><td>2.7</td><td>0.5</td><td>32.9</td><td>0.5</td></tr>
        <tr><td>Factor 2</td><td>Model 2</td><td>Materials</td><td>0.8</td><td>0.3</td><td>2.5</td><td>0.5</td><td>32.9</td><td>-0.5</td></tr>
      </tbody>
    </table>
  </main>
</section>

<!-- Screen 3 -->
<section class="screen screen--three">
  <nav class="topnav">
    <a style="left:54px">VANTIX</a>
    <a class="tab--active" style="left:99px;width:36px">250D</a>
    <a style="left:140px">83D</a>
    <a style="left:172px">42D</a>
    <a style="left:394px">MODELS</a>
    <a style="left:454px">SENSIVITIES</a>
    <a style="left:532px">FAVOURITES</a>
  </nav>
  <div class="quality">QUALITY</div>
  <div class="qlabel" style="left:112px">Threshold</div>
  <div class="qfield" style="left:175px">10</div>
  <div class="qlabel" style="left:285px">Threshold</div>
  <div class="qfield" style="left:348px">10</div>
  <div class="export export--new">EXPORT</div>
  <table class="grid grid--models">
    <colgroup><col style="width:71px"><col style="width:64px"><col style="width:65px"><col style="width:61px"><col style="width:41px"><col style="width:40px"><col style="width:39px"><col style="width:35px"><col style="width:34px"><col style="width:35px"><col style="width:38px"><col style="width:43px"></colgroup>
    <thead><tr><th class="sort">ID <svg width="6" height="4" viewBox="0 0 6 4"><path d="M0 0 H6 L3 4Z" fill="#fff"/></svg></th><th>Sector</th><th>Time</th><th>Quality</th><th>Stat 1</th><th>Stat 2</th><th>Stat 3</th><th>Stat 4</th><th>Stat 5</th><th>Stat 6</th><th>Stat 7</th><th>Stat 8</th></tr></thead>
    <tbody>
      <tr><td>Model 1</td><td>Materials</td><td>2019-07-03<br>12:15:00.000</td><td>30.2288</td><td>2.01574</td><td>23.305</td><td>-0.149368</td><td>22.3054</td><td>4.63714</td><td>0.945706</td><td>2.81949</td><td>2.60858</td></tr>
      <tr><td>Model 2</td><td>industrials</td><td>2019-07-03<br>12:15:00.000</td><td>32.8694</td><td>0.87307</td><td>32.185</td><td>-0.0336927</td><td>33.9911</td><td>11.5693</td><td>-0.472968</td><td>-0.830458</td><td>6.80646</td></tr>
      <tr><td>Model 3</td><td>Consumer<br>Discretionary</td><td>2019-07-03<br>12:15:00.000</td><td>30.2288</td><td>-0.569222</td><td>159.814</td><td>0.0252328</td><td>172.616</td><td>10.2875</td><td>-0.750396</td><td>-0.385309</td><td>4.69146</td></tr>
      <tr><td>Model 4</td><td>Information<br>Technology</td><td>2019-07-03<br>12:15:00.000</td><td>45.6856</td><td>0.412148</td><td>202.488</td><td>0.00849232</td><td>205.834</td><td>11.9094</td><td>-0.137913</td><td>0.449595</td><td>3.85106</td></tr>
      <tr><td>Model 5</td><td>Information<br>Technology</td><td>2019-07-03<br>12:15:00.000</td><td>75.7733</td><td>7.06728</td><td>188.605</td><td>0.016913</td><td>181.665</td><td>3.82241</td><td>0.981019</td><td>1.29847</td><td>3.34927</td></tr>
    </tbody>
  </table>
</section>

</body>
</html>
```